Design a single page Shopify store web page

We are looking to have a page designed for a single page Shopify store with 2 products. We already have a basic structure that we like, though we are open to suggestions. We are looking for somebody to provide a design/color scheme that we can then implement using Shopify's templating system. We can handle the implementation(HTML / CSS / jS) as we already have 2 web developers on the team, but have not been able to find a design we liked.

The job would consist of providing a mockup (photoshop or otherwise) and any vector graphics you choose to create for the site (we can provide product photos and other images).

You can also look at http://brickdune.com.au for some of our design direction we have used so far

Target Market(s)

Young Australian Males (18 - 49)

Industry/Entity Type

Store

Number of Pages Required

1 page

Font styles to use
Serif
Sans Serif

Requirements
Must have
• Single Page Design
• E-commerce Product Purchase
• Manly (whatever interpretation of that you have)

```html
<!DOCTYPE html>
<html lang="en">
<head>
<meta charset="utf-8">
<title>Brick Dune — Underwear &amp; Socks Delivered</title>
<link href="https://fonts.googleapis.com/css2?family=Open+Sans:wght@300;400;600;700&display=swap" rel="stylesheet">
<style>
:root{
  --ink:#1b1b1b;
  --nav:#1f1f1f;
  --footer:#1e1e1e;
  --sky:#00aeef;
  --sky-text:#1ab0ef;
  --white:#ffffff;
  --grey:#555555;
  --ring:#8a8a8a;
}
*{margin:0;padding:0;box-sizing:border-box}
html,body{width:1200px;height:2203px;overflow:hidden}
body{position:relative;font-family:"Open Sans",Arial,sans-serif;color:var(--ink);background:var(--white)}
.abs{position:absolute}
.center-text{text-align:center}

/* nav */
.site-nav{position:absolute;left:0;top:0;width:1200px;height:94px;background:var(--nav)}
.brand{position:absolute;left:132px;top:18px;font-size:31px;font-weight:700;color:var(--white);letter-spacing:-.5px}
.nav-link{position:absolute;top:29px;font-size:17px;color:var(--white);text-decoration:none}
.nav-link--accent{color:var(--sky-text)}

/* hero */
.hero{position:absolute;left:0;top:94px;width:1200px;height:486px;background:linear-gradient(180deg,#2e3036 0%,#26282c 55%,#1f2023 100%)}
.hero-shop{position:absolute;inset:0;background:linear-gradient(90deg,rgba(70,60,60,.35),rgba(50,55,70,.25),rgba(80,60,55,.35))}
.product-ring{position:absolute;width:244px;height:244px;border-radius:50%;border:4px solid var(--ring);background:#0c0c0c;overflow:hidden}
.product-ring .fill{width:100%;height:100%}
.hero-copy{position:absolute;left:490px;top:84px;width:600px;text-align:center;color:var(--white);font-size:32px;line-height:57px}
.hero-btn{position:absolute;left:701px;top:379px;width:176px;height:37px;background:var(--sky);color:var(--white);font-size:20px;line-height:37px;text-align:center}

/* sections */
.section-title{position:absolute;left:0;width:1200px;text-align:center;font-size:32px;font-weight:400}
.step{position:absolute;width:320px;text-align:center}
.step-photo{width:188px;height:188px;border-radius:50%;margin:0 auto}
.step-title{margin-top:12px;font-size:28px;font-weight:300;color:var(--sky-text)}
.step-text{margin-top:8px;font-size:13px;line-height:23px;color:var(--grey)}

/* plans */
.plans{position:absolute;left:0;top:1037px;width:1200px;height:585px;background:var(--sky)}
.plan-card{position:absolute;top:99px;width:475px;height:374px;background:var(--white);border-radius:4px}
.plan-name{position:absolute;left:0;top:14px;width:100%;text-align:center;font-size:31px;font-weight:300;color:var(--sky-text)}
.plan-main{position:absolute;left:19px;top:70px;width:282px;height:282px}
.plan-thumb{position:absolute;left:316px;width:140px;height:46px}
.plan-price{position:absolute;left:316px;top:225px;width:140px;text-align:center;font-size:34px;font-weight:300;color:var(--sky-text)}
.plan-btn{position:absolute;left:316px;top:302px;width:140px;height:47px;background:var(--sky);color:var(--white);font-size:20px;line-height:47px;text-align:center}
.perk{position:absolute;top:525px;font-size:16px;font-weight:700;color:var(--white);display:flex;align-items:center;gap:3px}

/* faq */
.faq-item{position:absolute;width:310px;text-align:center}
.faq-q{font-size:27px;font-weight:300;color:var(--sky-text);line-height:32px}
.faq-a{margin-top:10px;font-size:12.5px;line-height:22px;color:var(--grey)}

/* footer */
.site-footer{position:absolute;left:0;top:2120px;width:1200px;height:83px;background:var(--footer);color:var(--white);font-size:16px}
.footer-links{position:absolute;left:95px;top:29px}
.footer-mail{position:absolute;left:485px;top:29px}
.marks{position:absolute;left:700px;top:30px;display:flex;gap:10px}
.mark{display:flex;align-items:center;gap:4px;font-size:12px;color:var(--white)}
.mark-sq{width:14px;height:14px;background:var(--sky)}
</style>
</head>
<body>

<header class="site-nav">
  <div class="brand">Brick Dune</div>
  <a class="nav-link" style="left:460px" href="#how">How It Works</a>
  <a class="nav-link" style="left:617px" href="#plans">Plans</a>
  <a class="nav-link" style="left:711px" href="#faq">FAQ</a>
  <a class="nav-link" style="left:798px" href="#about">About us</a>
  <a class="nav-link nav-link--accent" style="left:921px" href="#signup">Signup Now</a>
</header>

<section class="hero">
  <div class="hero-shop" role="img" aria-label="Dimly lit menswear store interior with shelves of clothing and accessories"></div>
  <div class="product-ring" style="left:117px;top:51px">
    <div class="fill" role="img" aria-label="Grey trunks with orange waistband" style="background:radial-gradient(circle,#9a9a9a 0%,#6b6b6b 35%,#111 62%)"></div>
  </div>
  <div class="product-ring" style="left:316px;top:182px">
    <div class="fill" role="img" aria-label="Pair of dark grey socks with green print" style="background:radial-gradient(circle,#4a4a4a 0%,#333 40%,#0e0e0e 65%)"></div>
  </div>
  <div class="hero-copy">New Underwear and socks deliverd<br>to you door.<br>Every 3 or 6 months</div>
  <div class="hero-btn">Yes Please</div>
</section>

<h2 class="section-title" style="top:598px" id="how">How It Works</h2>
<div class="step" style="left:63px;top:683px">
  <div class="step-photo" role="img" aria-label="Collage of men's briefs in assorted colours" style="background:linear-gradient(135deg,#d9b59a,#6a5a8a 60%,#3a7a3a)"></div>
  <div class="step-title">Choose a Plan</div>
  <div class="step-text">Aenean sollicitudin, lorem quis bibendum<br>auctor nisi elit consequat ipsum, nec sagittis</div>
</div>
<div class="step" style="left:429px;top:683px">
  <div class="step-photo" role="img" aria-label="Five pack of boxed briefs" style="background:linear-gradient(135deg,#222,#3a5a9a 55%,#d8d8d8)"></div>
  <div class="step-title">Choose How Often</div>
  <div class="step-text">Llorem quis bibendum auctor nisi elit con<br>sequat ipsum, nec sagittis sem nibh id elit</div>
</div>
<div class="step" style="left:811px;top:683px">
  <div class="step-photo" role="img" aria-label="Stack of underwear waistbands and red socks" style="background:linear-gradient(135deg,#c9a94a,#b03040 35%,#1a2a4a 65%)"></div>
  <div class="step-title">Get Your Pack</div>
  <div class="step-text">Sollicitudin, lorem quis bibendum auctor nisi<br>elit consequat ipsum, nec sagittis sem nibh id</div>
</div>

<section class="plans" id="plans">
  <h2 class="section-title" style="top:16px;color:var(--white)">Plans</h2>

  <div class="plan-card" style="left:95px">
    <div class="plan-name">Comfort</div>
    <div class="plan-main" role="img" aria-label="Navy briefs worn by a model, torso only" style="background:linear-gradient(180deg,#c09a80,#8a6a58 45%,#1c1f30 70%,#a07a64)"></div>
    <div class="plan-thumb" style="top:71px" role="img" aria-label="Burgundy trunks" style="" ></div>
    <div class="plan-thumb" style="top:71px;background:linear-gradient(90deg,#d8cfc2,#7a2a30,#d8cfc2)" role="img" aria-label="Burgundy trunks"></div>
    <div class="plan-thumb" style="top:135px;background:linear-gradient(90deg,#d8cfc2,#c0202a,#d8cfc2)" role="img" aria-label="Red trunks"></div>
    <div class="plan-price">$30</div>
    <div class="plan-btn">GET IT</div>
  </div>

  <div class="plan-card" style="left:605px">
    <div class="plan-name">Style</div>
    <div class="plan-main" role="img" aria-label="Dark brown dress socks on a display form" style="background:linear-gradient(90deg,#5ec8ea,#3a3430 35%,#3a3430 65%,#5ec8ea)"></div>
    <div class="plan-thumb" style="top:71px;background:linear-gradient(90deg,#c48a4a,#2a3a6a,#c04a3a,#c48a4a)" role="img" aria-label="Patterned socks on timber floor"></div>
    <div class="plan-thumb" style="top:135px;background:linear-gradient(90deg,#8a9a8a,#b04a5a,#6a8a7a)" role="img" aria-label="Colourful socks on tiled floor"></div>
    <div class="plan-price">$30</div>
    <div class="plan-btn">GET IT</div>
  </div>

  <div class="perk" style="left:169px"><svg width="14" height="14" viewBox="0 0 14 14"><path d="M2 7.5l3 3 7-8" fill="none" stroke="#fff" stroke-width="2.2"/></svg>Free Shipping</div>
  <div class="perk" style="left:375px"><svg width="14" height="14" viewBox="0 0 14 14"><path d="M2 7.5l3 3 7-8" fill="none" stroke="#fff" stroke-width="2.2"/></svg>Easy Returns</div>
  <div class="perk" style="left:583px"><svg width="14" height="14" viewBox="0 0 14 14"><path d="M2 7.5l3 3 7-8" fill="none" stroke="#fff" stroke-width="2.2"/></svg>Cancel Whenever</div>
  <div class="perk" style="left:817px"><svg width="14" height="14" viewBox="0 0 14 14"><path d="M2 7.5l3 3 7-8" fill="none" stroke="#fff" stroke-width="2.2"/></svg>Satisfaction Guaranteed</div>
</section>

<h2 class="section-title" style="top:1658px" id="faq">FAQ</h2>
<div class="faq-item" style="left:86px;top:1744px">
  <div class="faq-q">What is Brick Dune?</div>
  <div class="faq-a">Aenean sollicitudin, lorem quis bibendum auctor<br>nisi elit consequat ipsum, nec sagittis sem nibh id<br>elit.Duis sed odio sit amet nibh vulputate cursus a</div>
</div>
<div class="faq-item" style="left:430px;top:1744px">
  <div class="faq-q">Shipping Policy?</div>
  <div class="faq-a">Aenean sollicitudin, lorem quis bibendum auctor<br>nisi elit consequat ipsum, nec sagittis sem nibh id<br>elit.Duis sed odio sit amet nibh vulputate cursus a</div>
</div>
<div class="faq-item" style="left:779px;top:1744px">
  <div class="faq-q">Return Policy?</div>
  <div class="faq-a">Aenean sollicitudin, lorem quis bibendum auctor<br>nisi elit consequat ipsum, nec sagittis sem nibh id<br>elit.Duis sed odio sit amet nibh vulputate cursus a</div>
</div>
<div class="faq-item" style="left:86px;top:1906px">
  <div class="faq-q">What is your<br>Satisfaction Guarantee?</div>
  <div class="faq-a">Aenean sollicitudin, lorem quis bibendum auctor<br>nisi elit consequat ipsum, nec sagittis sem nibh id<br>elit.Duis sed odio sit amet nibh vulputate cursus a</div>
</div>
<div class="faq-item" style="left:430px;top:1906px">
  <div class="faq-q">What is your<br>Satisfaction Guarantee?</div>
  <div class="faq-a">Aenean sollicitudin, lorem quis bibendum auctor<br>nisi elit consequat ipsum, nec sagittis sem nibh id<br>elit.Duis sed odio sit amet nibh vulputate cursus a</div>
</div>
<div class="faq-item" style="left:779px;top:1906px">
  <div class="faq-q">What is your<br>Satisfaction Guarantee?</div>
  <div class="faq-a">Aenean sollicitudin, lorem quis bibendum auctor<br>nisi elit consequat ipsum, nec sagittis sem nibh id<br>elit.Duis sed odio sit amet nibh vulputate cursus a</div>
</div>

<footer class="site-footer">
  <div class="footer-links">Shipping / Returns / Payment / Terms / Privacy</div>
  <div class="footer-mail">Holla@brickdune.com.au</div>
  <div class="marks">
    <span class="mark"><span class="mark-sq"></span>Pals</span>
    <span class="mark"><span class="mark-sq"></span>Chirp</span>
    <span class="mark"><span class="mark-sq"></span>Blogr</span>
    <span class="mark"><span class="mark-sq"></span>Snaps</span>
    <span class="mark"><span class="mark-sq"></span>Centa</span>
    <span class="mark"><span class="mark-sq"></span>Vesta</span>
    <span class="mark"><span class="mark-sq"></span>Orbit</span>
  </div>
</footer>

</body>
</html>
```